Book cover design, title is "Leave the Cubicle: Building Your Own Paycheck in One Year"

Design a cover for a book about freelancing. Example of my previous book's cover attached. Book title is "Leave the Cubicle: Building Your Own Paycheck in One Year". Looking to target people who have a 9-5 job but are seeking to try out freelancing as a way to supplement income and eventually quit their day job.

Target Market(s)

Looking to target people who have a 9-5 job but are seeking to try out freelancing as a way to supplement income and eventually quit their day job.

Industry/Entity Type

Consulting

Font styles to use
Serif
Sans Serif

Colors

Designer to choose colors to be used in the design.

Requirements
Must have
• I love these books covers...
• https://www.pagebarn.example/Tame-Notepile-Handbook-Sorting-Planning-ebook/dp/Q00XZRTMPA/ref=kl_ab?ie=UTF8
• https://www.pagebarn.example/Quiet-Dawn-Authors-Drafting-Doubles/dp/5830174926/ref=kl_ab?ie=UTF8
• https://www.pagebarn.example/Draft-True-Stories-Guide-Weeks-ebook/dp/Q00PL44KD7/ref=kl_ab?ie=UTF8
• https://www.pagebarn.example/Routine-Weaving-Tiny-Shifts-Moments/dp/1627093358/ref=kl_ab?ie=UTF8
• https://www.pagebarn.example/Sharpen-Each-Hour-Practical-ebook/dp/Q00WTN6HJS/ref=kl_ab?ie=UTF8
• https://www.pagebarn.example/Maker-Co-Complete-Thriving-Independent-ebook/dp/Q00918KVZE/ref=sr_1_4?ie=UTF8&qid=1627582273&sr=8-4&keywords=freelancing
Should not have
• Don't submit 3D renderings, just the front cover image please.

```html
<!DOCTYPE html>
<html lang="en">
<head>
<meta charset="utf-8">
<title>Leave the Cubicle – Book Cover</title>
<link rel="stylesheet" href="https://fonts.googleapis.com/css2?family=Marcellus+SC&family=Poiret+One&display=swap">
<style>
  :root {
    --page-bg: #d9d9db;
    --cover-bg: #efeff0;
    --desk-light: #f7f7f8;
    --desk-shade: #dcdcde;
    --band-black: #060608;
    --title-white: #ffffff;
    --bar-grey: #4b4b4d;
    --bar-text: #dedede;
    --author-ink: #111111;
  }
  * { margin: 0; padding: 0; box-sizing: border-box; }
  html, body {
    width: 1200px; height: 1200px; overflow: hidden;
    background: var(--page-bg);
  }
  .cover {
    position: absolute; left: 210px; top: 40px;
    width: 780px; height: 1120px;
    background: var(--cover-bg);
    overflow: hidden;
    box-shadow: 0 6px 24px rgba(0,0,0,0.18);
  }
  .cover-photo-top {
    position: absolute; left: 0; top: 0; width: 100%; height: 420px;
    background: linear-gradient(160deg, var(--desk-light) 0%, #e6e6e8 45%, #a9a6a2 100%);
  }
  .cover-photo-notepad {
    position: absolute; right: 0; top: 660px; width: 370px; height: 360px;
    background: linear-gradient(135deg, var(--desk-light) 0%, var(--desk-shade) 100%);
  }
  .title-band {
    position: absolute; left: 0; top: 0; width: 100%; height: 100%;
  }
  .title-band text {
    font-family: "Marcellus SC", serif;
    fill: var(--title-white);
    font-size: 92px;
  }
  .subtitle {
    position: absolute; left: 0; top: 730px;
    transform: rotate(-5deg); transform-origin: left top;
  }
  .subtitle-line {
    display: block; width: fit-content;
    background: var(--bar-grey);
    color: var(--bar-text);
    font-family: "Poiret One", sans-serif;
    font-size: 62px; line-height: 76px;
    text-transform: uppercase;
    padding: 0 12px 0 18px;
    margin-bottom: 10px;
    white-space: nowrap;
  }
  .author {
    position: absolute; left: 0; width: 100%; top: 1040px;
    text-align: center;
    font-family: "Marcellus SC", serif;
    font-size: 24px; letter-spacing: 1px;
    color: var(--author-ink);
    transform: rotate(-4deg);
  }
</style>
</head>
<body>
  <div class="cover">
    <div class="cover-photo-top" role="img" aria-label="Photo of a white keyboard, a grey fabric pouch and a black pen on a white desk"></div>
    <div class="cover-photo-notepad" role="img" aria-label="Photo of a spiral notepad with a pencil on a white desk"></div>

    <svg class="title-band" viewBox="0 0 780 1120" xmlns="http://www.w3.org/2000/svg">
      <polygon points="0,340 780,250 780,530 0,620" fill="var(--band-black)"/>
      <g transform="rotate(-6.58 390 440)">
        <text x="230" y="420">Leave the</text>
        <text x="190" y="525">Cubicle</text>
      </g>
    </svg>

    <div class="subtitle">
      <span class="subtitle-line">Building your own</span>
      <span class="subtitle-line">paycheck in</span>
      <span class="subtitle-line">one year</span>
    </div>

    <p class="author">Writers Name</p>
  </div>
</body>
</html>
```